Criação de Kit com 6 Layouts de Post para Redes Sociais (Facebook, Instagram e etc) para Saúde & Nutrição
" Consultório oftalmológico com ênfase em consultas oftalmológicas, exames complementares e cirurgias oculares "

```html
<!DOCTYPE html>
<html lang="pt-BR">
<head>
<meta charset="UTF-8">
<title>Post – Cirurgia oftalmológica</title>
<link href="https://fonts.googleapis.com/css2?family=Poppins:wght@400;500;600;700&display=swap" rel="stylesheet">
<style>
  :root{
    --navy:#16305a;
    --navy-deep:#0d1f3d;
    --teal-dark:#0b3b4a;
    --teal:#2d7f92;
    --teal-light:#8fd3e0;
    --gold:#c9a46a;
    --gold-light:#e4c995;
    --white:#ffffff;
    --text-soft:#d7e3f2;
  }
  *{margin:0;padding:0;box-sizing:border-box}
  html,body{width:1200px;height:1200px;overflow:hidden;background:var(--navy-deep)}
  .post{position:relative;width:1200px;height:1200px;overflow:hidden;font-family:'Poppins',sans-serif}
  .post__photo{
    position:absolute;inset:0;
    background:
      radial-gradient(ellipse 420px 520px at 900px 560px, rgba(143,211,224,.55), transparent 70%),
      radial-gradient(ellipse 380px 260px at 860px 330px, rgba(214,190,170,.45), transparent 70%),
      radial-gradient(circle 260px at 80px 120px, rgba(220,235,240,.35), transparent 70%),
      linear-gradient(135deg, #1f5a6a 0%, var(--teal-dark) 40%, #0f4656 65%, #1d6a7c 100%);
  }
  .post__shade{
    position:absolute;inset:0;
    background:linear-gradient(90deg, rgba(8,30,50,.55) 0%, rgba(8,30,50,.15) 55%, transparent 100%);
  }
  .card{
    position:absolute;left:192px;top:345px;width:444px;height:520px;
    background:var(--navy);
  }
  .card__badge{
    position:absolute;left:288px;top:288px;width:130px;height:130px;border-radius:50%;
    background:var(--navy);border:3px solid var(--gold);
  }
  .card__pill{
    position:absolute;left:236px;top:456px;height:42px;padding:0 20px;
    background:var(--gold-light);color:var(--navy-deep);border-radius:21px;
    font-size:22px;font-weight:500;line-height:42px;white-space:nowrap;
  }
  .card__title{
    position:absolute;left:236px;top:506px;color:var(--white);
    font-weight:600;line-height:1;
  }
  .card__title .big{display:block;font-size:72px;letter-spacing:-1px}
  .card__title .small{display:block;font-size:50px;margin-top:6px;letter-spacing:-.5px}
  .card__body{
    position:absolute;left:236px;top:650px;width:390px;color:var(--text-soft);
    font-size:21px;line-height:27px;font-weight:400;white-space:nowrap;
  }
  .cta{
    position:absolute;left:236px;top:806px;height:44px;padding:0 22px 0 8px;
    display:flex;align-items:center;gap:12px;
    background:var(--gold-light);color:var(--navy-deep);border-radius:22px;
    font-size:19px;font-weight:500;
  }
  .cta__icon{width:30px;height:30px}
  .brand{
    position:absolute;left:156px;top:905px;width:600px;text-align:center;color:var(--white);
  }
  .brand__mark{width:80px;height:80px;border-radius:50%;border:3px solid var(--white);margin:0 auto 34px}
  .brand__name{font-size:36px;font-weight:500;letter-spacing:1px;line-height:1}
  .brand__role{margin-top:18px;font-size:19px;font-weight:500;letter-spacing:11px}
</style>
</head>
<body>
<main class="post">
  <div class="post__photo" role="img" aria-label="Foto de uma cirurgiã oftalmológica com touca, máscara cirúrgica e óculos de proteção em sala de cirurgia"></div>
  <div class="post__shade"></div>

  <section class="card"></section>
  <div class="card__badge"></div>
  <div class="card__pill">Você já realizou</div>
  <h1 class="card__title"><span class="big">Cirurgia</span><span class="small">oftalmológica?</span></h1>
  <p class="card__body">Correções refrativas para<br>problemas de visão até cirurgias<br>para tratar condições como<br>catarata, estrabismo, glaucoma<br>e problemas das pálpebras.</p>
  <a class="cta">
    <svg class="cta__icon" viewBox="0 0 32 32"><circle cx="16" cy="16" r="16" fill="#16305a"/><path d="M13 10l6 6-6 6" stroke="#e4c995" stroke-width="3" fill="none" stroke-linecap="round" stroke-linejoin="round"/></svg>
    Fale conosco
  </a>

  <footer class="brand">
    <div class="brand__mark"></div>
    <div class="brand__name">Dra. Helena Vasconcelos</div>
    <div class="brand__role">OFTALMOLOGISTA</div>
  </footer>
</main>
</body>
</html>
```